Business card for event manager / organizer "waiter service"

Draft of a new valuable business card for my company.
Events, personnel service providers, festivals

```html
<!DOCTYPE html>
<html lang="de">
<head>
<meta charset="utf-8">
<title>Lenz Kellnerservice – Visitenkarte</title>
<link rel="stylesheet" href="https://fonts.googleapis.com/css2?family=Roboto:wght@300;400;700&display=swap">
<style>
  :root {
    --stage: #3b3b3e;
    --card: #050505;
    --card-sheen: #161616;
    --orange: #f07c1e;
    --white: #ffffff;
    --muted: #cfcfcf;
    --photo-dark: #0c0c0c;
    --photo-mid: #3a3a3a;
    --photo-light: #bfbfbf;
  }
  * { box-sizing: border-box; margin: 0; padding: 0; }
  html, body {
    width: 1200px; height: 913px; overflow: hidden;
    background: var(--stage);
    font-family: "Roboto", Arial, sans-serif;
  }
  .canvas { position: relative; width: 1200px; height: 913px; }
  .card {
    position: absolute; left: 250px; width: 700px; height: 400px;
    border-radius: 18px; overflow: hidden;
    background: linear-gradient(135deg, var(--card) 55%, var(--card-sheen) 100%);
    box-shadow: 0 3px 0 var(--orange), 0 14px 30px rgba(0,0,0,.45);
  }
  .card--front { top: 38px; }
  .card--back { top: 476px; }

  /* front */
  .portrait {
    position: absolute; left: 0; top: 0; width: 290px; height: 400px;
    background: radial-gradient(ellipse at 45% 70%, var(--photo-light) 0%, var(--photo-mid) 40%, var(--photo-dark) 75%);
  }
  .brand { position: absolute; display: flex; align-items: center; gap: 12px; }
  .brand__mark { background: var(--orange); flex: none; }
  .brand__name {
    color: var(--white); font-weight: 700; text-transform: uppercase; line-height: 1.05;
  }
  .brand__tagline { color: var(--muted); font-weight: 300; font-style: normal; }
  .card--front .brand { left: 330px; top: 48px; }
  .card--front .brand__mark { width: 52px; height: 52px; }
  .card--front .brand__name { font-size: 24px; }
  .card--front .brand__tagline { font-size: 11px; margin-top: 4px; }

  .person { position: absolute; left: 330px; top: 160px; }
  .person__name { color: var(--orange); font-size: 30px; font-weight: 400; letter-spacing: .5px; }
  .person__role { color: var(--white); font-size: 16px; font-weight: 300; margin-top: 2px; letter-spacing: 1px; }

  .contact { position: absolute; left: 330px; top: 250px; list-style: none; }
  .contact__item { display: flex; align-items: center; gap: 10px; color: var(--white); font-size: 17px; font-weight: 300; height: 25px; }
  .contact__icon { width: 14px; height: 14px; fill: none; stroke: var(--orange); stroke-width: 2; flex: none; }
  .contact__icon--solid { fill: var(--orange); stroke: none; }

  /* back */
  .card--back .brand { left: 160px; top: 115px; gap: 22px; }
  .card--back .brand__mark { width: 100px; height: 100px; }
  .card--back .brand__name { font-size: 40px; }
  .card--back .brand__tagline { font-size: 16px; margin-top: 8px; }
  .social { position: absolute; left: 160px; bottom: 52px; display: flex; align-items: center; gap: 10px; color: var(--white); font-size: 20px; font-weight: 300; }
  .social__dot { width: 16px; height: 16px; border-radius: 50%; background: var(--orange); }
</style>
</head>
<body>
<main class="canvas">
  <section class="card card--front" aria-label="Vorderseite">
    <div class="portrait" role="img" aria-label="Foto des Inhabers in Kellnerweste mit Tablett und Sektgläsern"></div>
    <div class="brand">
      <div class="brand__mark"></div>
      <div>
        <div class="brand__name">Lenz<br>Kellnerservice</div>
        <div class="brand__tagline">…damit Ihr Fest rundum gelingt!</div>
      </div>
    </div>
    <div class="person">
      <h1 class="person__name">LUKAS BRENNECKE</h1>
      <p class="person__role">INHABER</p>
    </div>
    <ul class="contact">
      <li class="contact__item"><svg class="contact__icon contact__icon--solid" viewBox="0 0 24 24"><path d="M6.6 10.8a15 15 0 0 0 6.6 6.6l2.2-2.2a1 1 0 0 1 1-.25 11.4 11.4 0 0 0 3.6.57 1 1 0 0 1 1 1V20a1 1 0 0 1-1 1A17 17 0 0 1 3 4a1 1 0 0 1 1-1h3.5a1 1 0 0 1 1 1c0 1.25.2 2.45.57 3.6a1 1 0 0 1-.25 1z"/></svg>02361 555 21 40</li>
      <li class="contact__item"><svg class="contact__icon contact__icon--solid" viewBox="0 0 24 24"><path d="M6.6 10.8a15 15 0 0 0 6.6 6.6l2.2-2.2a1 1 0 0 1 1-.25 11.4 11.4 0 0 0 3.6.57 1 1 0 0 1 1 1V20a1 1 0 0 1-1 1A17 17 0 0 1 3 4a1 1 0 0 1 1-1h3.5a1 1 0 0 1 1 1c0 1.25.2 2.45.57 3.6a1 1 0 0 1-.25 1z"/></svg>0171 555 83 27</li>
      <li class="contact__item"><svg class="contact__icon" viewBox="0 0 24 24"><rect x="3" y="5" width="18" height="14" rx="1"/><path d="M3 6l9 7 9-7"/></svg>info@lenz-kellnerservice.de</li>
      <li class="contact__item"><svg class="contact__icon" viewBox="0 0 24 24"><circle cx="12" cy="12" r="9"/><path d="M3 12h18M12 3c3 3 3 15 0 18M12 3c-3 3-3 15 0 18"/></svg>www.lenz-kellnerservice.de</li>
      <li class="contact__item"><svg class="contact__icon contact__icon--solid" viewBox="0 0 24 24"><path d="M12 2a7 7 0 0 0-7 7c0 5 7 13 7 13s7-8 7-13a7 7 0 0 0-7-7zm0 9.5A2.5 2.5 0 1 1 12 6.5a2.5 2.5 0 0 1 0 5z"/></svg>Birkenweg 12, 45657 Musterstadt</li>
    </ul>
  </section>

  <section class="card card--back" aria-label="Rückseite">
    <div class="brand">
      <div class="brand__mark"></div>
      <div>
        <div class="brand__name">Lenz<br>Kellnerservice</div>
        <div class="brand__tagline">…damit Ihr Fest rundum gelingt!</div>
      </div>
    </div>
    <div class="social"><span class="social__dot"></span>www.social.example/lenzkellnerservice</div>
  </section>
</main>
</body>
</html>
```